New business card/stationary for a consulting company

I am looking for a clean and very professional looking business card for my consulting company as well as corresponding stationary. I am uploading our logo. I like simple and powerful for the feel. No graphics but I am open on everything else. Below is my contact information but would like the final to be in a version I can add my employees information into and print. Thank you.

Daniel Whitcombe
dan@ferncliffadvisory.com
2870 North 9th Avenue, Summit Floor, Elm Ridge, Illinois 60531
www.ferncliffadvisory.com

Industry/Entity Type

Consulting

Contact Information for Business Card

Daniel Whitcombe
dan@ferncliffadvisory.com
www.ferncliffadvisory.com

Font styles to use
Serif
Sans Serif

Requirements
Must have
• Our logo and the business card details.
Nice to have
• our website www.ferncliffadvisory.com

```html
<!DOCTYPE html>
<html lang="en">
<head>
<meta charset="utf-8">
<title>Ferncliff Advisory — Business Card</title>
<link rel="stylesheet" href="https://fonts.googleapis.com/css2?family=Lato:wght@400;700&family=Oswald:wght@500&display=swap">
<style>
  :root {
    --backdrop: #3a3a3c;
    --card-navy: #07066b;
    --ink-white: #ffffff;
    --card-w: 600px;
    --card-h: 343px;
  }
  * { box-sizing: border-box; margin: 0; padding: 0; }
  html, body {
    width: 1200px;
    height: 900px;
    overflow: hidden;
    background: var(--backdrop);
  }
  .stage {
    position: relative;
    width: 1200px;
    height: 900px;
  }
  .card {
    position: absolute;
    left: 300px;
    width: var(--card-w);
    height: var(--card-h);
    background: var(--card-navy);
    color: var(--ink-white);
    box-shadow: 0 10px 24px rgba(0, 0, 0, 0.35);
  }
  .card--front { top: 75px; }
  .card--back { top: 482px; }

  /* Front */
  .brand {
    position: absolute;
    top: 104px;
    left: 0;
    width: 100%;
    text-align: center;
  }
  .brand__mark {
    display: inline-block;
    width: 22px;
    height: 22px;
    background: var(--ink-white);
    margin-bottom: 14px;
  }
  .brand__name {
    font-family: "Lato", sans-serif;
    font-weight: 400;
    font-size: 34px;
    letter-spacing: 3px;
    text-transform: uppercase;
    line-height: 1;
  }
  .front__web {
    position: absolute;
    top: 236px;
    left: 0;
    width: 100%;
    text-align: center;
    font-family: "Lato", sans-serif;
    font-size: 15px;
    letter-spacing: 1.5px;
  }

  /* Back */
  .holder-name {
    position: absolute;
    left: 40px;
    top: 130px;
    font-family: "Oswald", sans-serif;
    font-weight: 500;
    font-size: 34px;
    letter-spacing: -0.5px;
    text-transform: uppercase;
    line-height: 1;
  }
  .divider {
    position: absolute;
    left: 300px;
    top: 96px;
    width: 1px;
    height: 150px;
    background: var(--ink-white);
  }
  .contact {
    position: absolute;
    left: 322px;
    top: 100px;
    font-family: "Lato", sans-serif;
    font-size: 15px;
    line-height: 21px;
    list-style: none;
  }
  .contact__row {
    display: flex;
    align-items: center;
    gap: 8px;
    white-space: nowrap;
  }
  .contact__row--plain { padding-left: 22px; }
  .contact__icon { width: 14px; height: 14px; flex: none; }
</style>
</head>
<body>
<main class="stage">
  <section class="card card--front" aria-label="Card front">
    <div class="brand">
      <span class="brand__mark"></span>
      <p class="brand__name">Ferncliff Advisory</p>
    </div>
    <p class="front__web">www.ferncliffadvisory.com</p>
  </section>

  <section class="card card--back" aria-label="Card back">
    <h1 class="holder-name">Daniel Whitcombe</h1>
    <span class="divider"></span>
    <ul class="contact">
      <li class="contact__row contact__row--plain">2870 North 9th Avenue</li>
      <li class="contact__row contact__row--plain">Summit Floor</li>
      <li class="contact__row contact__row--plain">Elm Ridge, Illinois 60531</li>
      <li class="contact__row">
        <svg class="contact__icon" viewBox="0 0 14 14" aria-hidden="true">
          <rect x="0.5" y="3" width="13" height="9" fill="#fff"/>
          <path d="M0.5 3 L7 8 L13.5 3" fill="none" stroke="#07066b" stroke-width="1.2"/>
        </svg>
        dan@ferncliffadvisory.com
      </li>
      <li class="contact__row">
        <svg class="contact__icon" viewBox="0 0 14 14" aria-hidden="true">
          <circle cx="7" cy="7" r="6.2" fill="#fff"/>
          <g fill="none" stroke="#07066b" stroke-width="0.9">
            <ellipse cx="7" cy="7" rx="2.6" ry="6.2"/>
            <line x1="0.8" y1="7" x2="13.2" y2="7"/>
            <line x1="1.8" y1="4" x2="12.2" y2="4"/>
            <line x1="1.8" y1="10" x2="12.2" y2="10"/>
          </g>
        </svg>
        www.ferncliffadvisory.com
      </li>
    </ul>
  </section>
</main>
</body>
</html>
```